Redesign of agriculture and industrial webshop.

We are a chemical company that develops and produces all kinds of liquids. Cleaning products but also agriculture health products are our specialty. For both of them we have seperate webshops. www.brimfeldchemics.com/agriculture and www.brimfeldchemics.com/industrials. Both working with wordpress and visual composer to create the content. We'd like a modern and new professional redesign of the webshop to optimize sales and generating new clients. We have just redesigned our main page www.brimfeldchemics.com, this is not a webshop so it has different functions. But we'd like to take the choice of color to match the webshop colors. If you need any source documents, please let me know.

Target Market(s)

Agriculture market in the Netherlands and Industrials cleaning, lubrication market in The Netherlands

Industry/Entity Type

Agriculture

Number of Pages Required

2 page

Requirements
Must have
• Marketing strategies, colors, market segment, webshop look, webshop optimization for sales.
• Please design a homepages, product page, contact page and about us page for both webshops.

```html
<!DOCTYPE html>
<html lang="en">
<head>
<meta charset="utf-8">
<title>Brimfeld – Cattle Products</title>
<link href="https://fonts.googleapis.com/css2?family=Open+Sans:wght@400;600;700&family=Roboto:wght@400;500&family=Tauri&display=swap" rel="stylesheet">
<style>
:root{
  --green:#5a9a2c;
  --green-dark:#3f7d1a;
  --orange:#f4620f;
  --orange-dark:#d94f08;
  --ink:#222;
  --grey:#777;
  --line:#d9d9d9;
  --bg:#f7f7f5;
}
*{margin:0;padding:0;box-sizing:border-box}
html,body{width:731px;height:1200px;overflow:hidden}
body{position:relative;background:var(--bg);font-family:"Open Sans",sans-serif;color:var(--ink)}
.topbar{position:absolute;left:0;top:0;width:731px;height:24px;background:#fff;border-bottom:1px solid #e5e5e5;font:400 8px "Roboto",sans-serif}
.lang{position:absolute;left:110px;top:0;width:52px;height:24px;background:#e8e8e8;display:flex;align-items:center;justify-content:center;gap:3px}
.lang i{display:block;width:12px;height:8px;background:#2b4a9a}
.call{position:absolute;left:196px;top:8px;display:flex;gap:3px;align-items:center}
.call b{font-weight:400;color:var(--green)}
.account{position:absolute;right:111px;top:8px}
.header{position:absolute;left:0;top:24px;width:731px;height:64px;background:#fff}
.logo{position:absolute;left:113px;top:18px;font:400 26px "Tauri",sans-serif;color:var(--orange);letter-spacing:1px}
.search{position:absolute;left:275px;top:22px;width:198px;height:21px;border:1px solid #aaa;background:#f5f5f5;font:400 8px "Roboto",sans-serif;color:#666;padding:6px 0 0 22px}
.search svg{position:absolute;left:8px;top:5px}
.cart{position:absolute;left:548px;top:24px;display:flex;align-items:center;gap:5px;font:400 10px "Roboto",sans-serif}
.nav{position:absolute;left:0;top:88px;width:731px;height:26px;background:var(--green);font:500 8px "Roboto",sans-serif;color:#fff}
.nav a{position:absolute;top:0;height:26px;line-height:26px;padding:0 12px;text-decoration:none;color:#fff}
.nav a.active{background:var(--orange)}
.hero{position:absolute;left:0;top:114px;width:731px;height:256px;background:linear-gradient(#3e6fb0 0%,#7ea5cf 35%,#6f9a45 60%,#4f7f2a 100%)}
.hero h1{position:absolute;left:0;right:0;top:86px;text-align:center;font:700 29px "Open Sans",sans-serif;color:#fff;letter-spacing:1px}
.hero svg{position:absolute;left:0;bottom:0;display:block}
.section-title{position:absolute;left:0;right:0;top:396px;text-align:center;font:400 20px "Tauri",sans-serif;letter-spacing:1px}
.card{position:absolute;width:120px;height:212px;background:#fff;border:1px solid var(--line);box-shadow:0 1px 3px rgba(0,0,0,.12);text-align:center}
.card .shot{position:absolute;left:35px;top:14px;width:50px;height:82px;border-radius:6px}
.card h3{position:absolute;left:0;right:0;top:113px;font:400 10px "Tauri",sans-serif;color:var(--green-dark)}
.card p{position:absolute;left:10px;right:10px;top:128px;font:400 7px/11px "Open Sans",sans-serif;color:var(--grey)}
.card .price{position:absolute;left:0;right:0;top:155px;font:700 12px "Open Sans",sans-serif;color:var(--green-dark)}
.card .buy{position:absolute;left:23px;top:177px;width:78px;height:20px;border-radius:10px;background:var(--orange);color:#fff;font:500 8px/20px "Roboto",sans-serif}
.more{position:absolute;left:321px;top:922px;width:92px;height:25px;border:2px solid var(--green);border-radius:13px;text-align:center;font:500 10px/21px "Roboto",sans-serif;color:var(--green-dark)}
.footer{position:absolute;left:0;top:1007px;width:731px;height:159px;background:linear-gradient(#f2600e,#f57a20);color:#fff}
.footer h4{position:absolute;top:36px;font:700 8px "Open Sans",sans-serif}
.footer ul{position:absolute;top:59px;list-style:none;font:400 8px/15px "Open Sans",sans-serif}
.news p{position:absolute;left:118px;top:59px;font-size:8px}
.email{position:absolute;left:118px;top:74px;width:137px;height:22px;border:1px solid #ffd0b0;font-size:7px;padding:6px 8px}
.subscribe{position:absolute;left:118px;top:103px;width:72px;height:19px;background:var(--green);font:700 7px/19px "Open Sans",sans-serif;text-align:center}
.social{position:absolute;left:530px;top:54px;display:flex;gap:3px}
.social i{display:block;width:19px;height:19px;border:1px solid #fff;border-radius:50%}
.pay{position:absolute;left:530px;top:94px;display:flex;gap:5px}
.pay i{display:block;width:17px;height:11px;background:#fff;border-radius:1px}
.copy{position:absolute;left:0;top:1166px;width:731px;height:34px;background:var(--orange-dark);color:#fff;font:400 7px/14px "Open Sans",sans-serif;text-align:center;padding-top:6px}
</style>
</head>
<body>
<div class="topbar">
  <div class="lang"><i></i>ENG
    <svg width="6" height="4" viewBox="0 0 6 4"><path d="M0 0l3 3 3-3" stroke="#333" fill="none"/></svg></div>
  <div class="call"><svg width="9" height="9" viewBox="0 0 10 10"><path d="M2 1l2 2-1 1.5c.8 1.5 1.8 2.5 3.5 3.5L8 6l2 2-1.5 1.5C4 9 1 6 .5 1.5z" fill="#444"/></svg>CALL US <b>+31 400 12 34 56</b></div>
  <div class="account">My Account &nbsp;|&nbsp; Wishlist &nbsp;|&nbsp; Login &nbsp;|&nbsp; Checkout</div>
</div>

<header class="header">
  <div class="logo">BRIMFELD</div>
  <div class="search"><svg width="10" height="10" viewBox="0 0 10 10"><circle cx="4" cy="4" r="3" stroke="#666" fill="none" stroke-width="1.4"/><path d="M6.3 6.3L9.5 9.5" stroke="#666" stroke-width="1.4"/></svg>Search here...</div>
  <div class="cart"><svg width="20" height="16" viewBox="0 0 20 16"><path d="M1 5h18l-2 10H3z" fill="var(--orange)"/><path d="M5 5l3-4M15 5l-3-4" stroke="var(--orange)" stroke-width="1.5" fill="none"/><path d="M6 8v4M10 8v4M14 8v4" stroke="#fff" stroke-width="1.2"/></svg>0 ITEMS</div>
</header>

<nav class="nav">
  <a style="left:117px">HOME</a>
  <a style="left:176px">ABOUT US</a>
  <a class="active" style="left:234px">CATTLE</a>
  <a style="left:283px">POULTRY</a>
  <a style="left:339px">CROP</a>
  <a style="left:379px">AUXILIARY PRODUCTS</a>
  <a style="left:484px">KNOWLEDGE</a>
  <a style="left:551px">PACKAGING</a>
</nav>

<section class="hero" role="img" aria-label="Herd of black and white dairy cows standing in a green meadow under a blue sky">
  <h1>PRODUCTS</h1>
  <svg width="731" height="60" viewBox="0 0 731 60" preserveAspectRatio="none"><path d="M0 60V48Q365 0 731 48V60Z" fill="var(--bg)"/></svg>
</section>

<h2 class="section-title">CATTLE PRODUCTS</h2>

<div class="card" style="left:113px;top:453px"><div class="shot" role="img" aria-label="Blue spray bottle" style="background:linear-gradient(#cfe8f2,#7cbfdc)"></div><h3>PRODUCT NAME</h3><p>Fusce tellus Sed metus augue convallis et vehicula</p><div class="price">£357.50</div><div class="buy">Shop Now</div></div>
<div class="card" style="left:244px;top:453px"><div class="shot" role="img" aria-label="White powder bag" style="background:linear-gradient(#f4f4f4,#d8d8d8)"></div><h3>PRODUCT NAME</h3><p>Fusce tellus Sed metus augue convallis et vehicula</p><div class="price">£357.50</div><div class="buy">Shop Now</div></div>
<div class="card" style="left:373px;top:453px"><div class="shot" role="img" aria-label="Pink bottle labelled Bio A" style="background:linear-gradient(#e6c8d0,#8cbf4a)"></div><h3>BIO A</h3><p>Fusce tellus Sed metus augue convallis et vehicula</p><div class="price">£357.50</div><div class="buy">Shop Now</div></div>
<div class="card" style="left:505px;top:453px"><div class="shot" role="img" aria-label="Pink jerrycan of cleaning liquid" style="background:linear-gradient(#f6c6cc,#8cbf4a)"></div><h3>PRODUCT NAME</h3><p>Fusce tellus Sed metus augue convallis et vehicula</p><div class="price">£357.50</div><div class="buy">Shop Now</div></div>

<div class="card" style="left:111px;top:686px"><div class="shot" role="img" aria-label="Pink bottle labelled Bio Gin" style="background:linear-gradient(#e6c8d0,#8cbf4a)"></div><h3>BIO GIN</h3><p>Fusce tellus Sed metus augue convallis et vehicula</p><div class="price">£357.50</div><div class="buy">Shop Now</div></div>
<div class="card" style="left:243px;top:686px"><div class="shot" role="img" aria-label="Amber bottle of liquid" style="background:linear-gradient(#e58a3c,#a6420c)"></div><h3>PRODUCT NAME</h3><p>Fusce tellus Sed metus augue convallis et vehicula</p><div class="price">£357.50</div><div class="buy">Shop Now</div></div>
<div class="card" style="left:372px;top:686px"><div class="shot" role="img" aria-label="Pink bottle labelled Bio C" style="background:linear-gradient(#e6c8d0,#8cbf4a)"></div><h3>BIO C</h3><p>Fusce tellus Sed metus augue convallis et vehicula</p><div class="price">£357.50</div><div class="buy">Shop Now</div></div>
<div class="card" style="left:503px;top:686px"><div class="shot" role="img" aria-label="Pink bottle labelled Bio D" style="background:linear-gradient(#e6c8d0,#8cbf4a)"></div><h3>BIO D</h3><p>Fusce tellus Sed metus augue convallis et vehicula</p><div class="price">£357.50</div><div class="buy">Shop Now</div></div>

<div class="more">View More</div>

<footer class="footer">
  <div class="news"><h4 style="left:118px">SIGN UP NEWSLETTER</h4><p>Please sign up for newsletter</p></div>
  <div class="email">Email address</div>
  <div class="subscribe">SUBSCRIBE</div>
  <h4 style="left:292px">COMPANY</h4>
  <ul style="left:292px"><li>Home</li><li>About Us</li><li>Our Producs</li><li>Cattle</li></ul>
  <h4 style="left:366px">PRODUCTS</h4>
  <ul style="left:368px"><li>Poultry</li><li>Crop</li><li>Auxiliary Proudcts</li><li>Knowledge</li></ul>
  <h4 style="left:454px">RESOURCES</h4>
  <ul style="left:457px"><li>My Account</li><li>Cart</li><li>Support</li><li>Contact Us</li></ul>
  <h4 style="left:530px">FOLLOW US</h4>
  <div class="social"><i></i><i></i><i></i><i></i></div>
  <div class="pay"><i></i><i></i><i></i><i></i><i></i></div>
</footer>
<div class="copy">© 2018 Company Name &nbsp;All rights reserved</div>
</body>
</html>
```